Looking for a modern, Professional business card design

We have a simple business card, but are looking for a more modern, professional look. A sample of the basic card is attached as well as the logo. We would also like to add that we offer:
Struggling with your finances?
- Learn to become debt free
- Discover the power of cash
- Control your money instead of it controlling you
Let us help you achieve a new level of financial freedom!
Also, we would like to have a "SPECIAL OFFER!: FREE 30 minute consultation"
Financial Planning

```html
<!DOCTYPE html>
<html lang="en">
<head>
<meta charset="utf-8">
<title>Clearpath Money Coaching – Business Card</title>
<link href="https://fonts.googleapis.com/css2?family=Open+Sans:ital,wght@0,400;0,600;0,700;1,700&display=swap" rel="stylesheet">
<style>
  :root {
    --backdrop: #2e3135;
    --green-deep: #3f9a2a;
    --green-mid: #5cb82f;
    --green-light: #8fd14a;
    --green-text: #4aa32b;
    --white: #ffffff;
    --paper: #f7f7f7;
    --ink: #1e1e1e;
  }
  * { margin: 0; padding: 0; box-sizing: border-box; }
  html, body {
    width: 1200px;
    height: 864px;
    overflow: hidden;
    background: var(--backdrop);
    font-family: "Open Sans", Arial, sans-serif;
  }
  .card-sheet {
    position: absolute;
    top: 277px;
    left: 40px;
    display: flex;
    gap: 40px;
  }
  .card {
    position: relative;
    width: 540px;
    height: 309px;
    overflow: hidden;
  }

  /* Front: offer side */
  .card--offer {
    background: linear-gradient(125deg, var(--green-mid) 0%, var(--green-deep) 55%, var(--green-mid) 100%);
    color: var(--white);
    text-align: center;
  }
  .offer-art {
    position: absolute;
    right: 0;
    top: 0;
    width: 200px;
    height: 309px;
    background: radial-gradient(ellipse at 60% 40%, rgba(170, 230, 90, 0.55) 0%, rgba(120, 200, 60, 0.25) 45%, rgba(90, 180, 50, 0) 75%);
  }
  .offer-content {
    position: relative;
    padding-top: 40px;
  }
  .offer-heading {
    font-size: 17px;
    font-weight: 700;
    font-style: italic;
    text-decoration: underline;
    text-underline-offset: 3px;
    margin-bottom: 14px;
  }
  .offer-points {
    list-style: none;
    font-size: 13.5px;
    line-height: 1.4;
    margin-bottom: 16px;
  }
  .offer-pitch {
    font-size: 13.5px;
    font-weight: 700;
    font-style: italic;
    line-height: 1.4;
  }
  .offer-band {
    position: absolute;
    left: 0;
    right: 0;
    top: 232px;
    height: 36px;
    background: var(--white);
    color: var(--green-text);
    font-size: 15px;
    font-weight: 700;
    line-height: 36px;
    text-align: center;
  }

  /* Back: contact side */
  .card--contact {
    background: linear-gradient(135deg, var(--white) 0%, var(--paper) 100%);
    color: var(--ink);
  }
  .brand {
    position: absolute;
    top: 62px;
    right: 34px;
    display: flex;
    align-items: center;
    gap: 10px;
  }
  .brand-dot {
    width: 22px;
    height: 22px;
    border-radius: 50%;
    background: var(--green-mid);
  }
  .brand-name {
    font-size: 21px;
    font-weight: 700;
    color: var(--green-text);
    letter-spacing: 0.5px;
  }
  .person {
    position: absolute;
    left: 34px;
    top: 132px;
  }
  .person-name {
    font-size: 19px;
    font-weight: 600;
    color: var(--green-text);
  }
  .person-role {
    font-size: 14px;
    color: var(--ink);
  }
  .divider {
    position: absolute;
    left: 200px;
    right: 0;
    top: 184px;
    height: 1.5px;
    background: var(--green-mid);
  }
  .contact-list {
    position: absolute;
    right: 34px;
    top: 204px;
    list-style: none;
    text-align: right;
    font-size: 14px;
    line-height: 1.6;
  }
  .contact-list li {
    display: flex;
    align-items: center;
    justify-content: flex-end;
    gap: 8px;
  }
  .contact-icon {
    width: 12px;
    height: 12px;
    fill: var(--green-mid);
  }
</style>
</head>
<body>
  <main class="card-sheet">
    <section class="card card--offer">
      <div class="offer-art" role="img" aria-label="Soft abstract green shapes decorating the card"></div>
      <div class="offer-content">
        <h2 class="offer-heading">Struggling with your finances?</h2>
        <ul class="offer-points">
          <li>Learn to become debt free</li>
          <li>Discover the power of cash</li>
          <li>Control your money instead of it controlling you</li>
        </ul>
        <p class="offer-pitch">Let us help you achieve a new<br>level of financial freedom!</p>
      </div>
      <div class="offer-band">SPECIAL OFFER!: FREE 30 minute consultation</div>
    </section>

    <section class="card card--contact">
      <div class="brand">
        <span class="brand-dot"></span>
        <span class="brand-name">CLEARPATH MONEY COACHING</span>
      </div>
      <div class="person">
        <p class="person-name">Daniel R. Hale</p>
        <p class="person-role">Personal Financial Coach</p>
      </div>
      <div class="divider"></div>
      <ul class="contact-list">
        <li>(555) 014-2290
          <svg class="contact-icon" viewBox="0 0 24 24" aria-hidden="true"><path d="M6.6 10.8a15.1 15.1 0 0 0 6.6 6.6l2.2-2.2c.3-.3.7-.4 1-.2 1.1.4 2.3.6 3.6.6.6 0 1 .4 1 1V20c0 .6-.4 1-1 1A17 17 0 0 1 3 4c0-.6.4-1 1-1h3.5c.6 0 1 .4 1 1 0 1.3.2 2.5.6 3.6.1.3 0 .7-.2 1z"/></svg>
        </li>
        <li>daniel@clearpathmoney.com
          <svg class="contact-icon" viewBox="0 0 24 24" aria-hidden="true"><path d="M2 5h20v14H2z M2 5l10 8 10-8" stroke="#fff" stroke-width="1.5"/></svg>
        </li>
        <li>www.clearpathmoney.com
          <svg class="contact-icon" viewBox="0 0 24 24" aria-hidden="true"><circle cx="12" cy="12" r="10"/><path d="M2 12h20M12 2c3 3 3 17 0 20M12 2c-3 3-3 17 0 20" stroke="#fff" stroke-width="1.3" fill="none"/></svg>
        </li>
      </ul>
    </section>
  </main>
</body>
</html>
```